English and Spanish Language School Needs a Business Card

Need a business card design a startup company called Maribel Language School. The company will offer English and Spanish conversational level courses designed to make the learner feel comfortable with grammar and vocabulary. We would like to see a logo with some colour that should communicate learning, growth.

Target Market(s)

Consumers and businesses

Industry/Entity Type

Education

Contact Information for Business Card

TBD

Font styles to use
Serif

Requirements
Must have
• Include the following
• Logo
• Name
• Title
• Cellphone Number
• Office Phone number
• Email address
• Office Address

```html
<!DOCTYPE html>
<html lang="en">
<head>
<meta charset="UTF-8">
<title>Maribel Language School – Business Card</title>
<link rel="stylesheet" href="https://fonts.googleapis.com/css2?family=Open+Sans:wght@400;600;700&display=swap">
<style>
  :root {
    --backdrop: #dcd8d5;
    --card-face: #f4f2f1;
    --brand-red: #c91f27;
    --brand-teal: #01a0ad;
    --ink-light: #ffffff;
  }
  * { margin: 0; padding: 0; box-sizing: border-box; }
  html, body {
    width: 1200px;
    height: 900px;
    overflow: hidden;
    background: var(--backdrop);
    font-family: "Open Sans", Arial, sans-serif;
  }
  .stage { position: relative; width: 1200px; height: 900px; }

  .card {
    position: absolute;
    background: var(--card-face);
    box-shadow: 0 2px 6px rgba(0,0,0,0.12);
    overflow: hidden;
  }
  .card--front { left: 238px; top: 62px; width: 555px; height: 343px; }
  .card--back  { left: 459px; top: 519px; width: 560px; height: 342px; }

  .brand {
    position: absolute;
    color: var(--brand-red);
    font-weight: 700;
    line-height: 1;
  }
  .card--front .brand { left: 114px; top: 48px; }
  .brand__name { display: block; font-size: 78px; letter-spacing: -1px; }
  .brand__tagline { display: block; font-size: 21px; margin-top: 4px; margin-left: 28px; }

  .card--back .brand {
    left: 116px; top: 52px;
    opacity: 0.28;
    transform: scaleX(-1);
  }

  .band {
    position: absolute;
    left: 0; right: 0; bottom: 0;
  }
  .band--red { top: 185px; background: var(--brand-red); }
  .band--teal { top: 186px; background: var(--brand-teal); }

  .holder {
    position: absolute;
    right: 313px; top: 52px;
    text-align: right;
    color: var(--ink-light);
  }
  .holder__name { font-size: 17px; font-weight: 600; line-height: 22px; }
  .holder__title { font-size: 14px; line-height: 19px; }

  .contacts {
    position: absolute;
    left: 266px; top: 44px;
    list-style: none;
    color: var(--ink-light);
    font-size: 14.5px;
  }
  .contacts li { display: flex; align-items: center; height: 20.5px; }
  .contacts svg { width: 12px; height: 12px; margin-right: 9px; fill: var(--ink-light); }

  .address {
    position: absolute;
    left: 0; right: 0; top: 76px;
    text-align: center;
    color: var(--ink-light);
    font-size: 14.5px;
  }
</style>
</head>
<body>
<main class="stage">
  <section class="card card--front">
    <div class="brand">
      <span class="brand__name">Maribel</span>
      <span class="brand__tagline">Language School</span>
    </div>
    <div class="band band--red">
      <div class="holder">
        <p class="holder__name">Daniel Reyes</p>
        <p class="holder__title">Managing Director</p>
      </div>
      <ul class="contacts">
        <li>
          <svg viewBox="0 0 12 12" aria-hidden="true"><path d="M2.4 0.6l2 2.2-1.1 1.4c.7 1.6 2 2.9 3.6 3.6l1.4-1.1 2.2 2-1.3 1.9C5 10.4 1.6 7 1 1.9z"/></svg>
          044-210 375 918
        </li>
        <li>
          <svg viewBox="0 0 12 12" aria-hidden="true"><path d="M3.5 0h5a1 1 0 0 1 1 1v10a1 1 0 0 1-1 1h-5a1 1 0 0 1-1-1V1a1 1 0 0 1 1-1zm.6 1.6v7.6h3.8V1.6zM6 9.9a.7.7 0 1 0 0 1.4.7.7 0 0 0 0-1.4z"/></svg>
          hello@maribelschool.com
        </li>
        <li>
          <svg viewBox="0 0 12 12" aria-hidden="true"><path d="M1 3h10v6.5H1zm.9.8L6 6.6l4.1-2.8z"/></svg>
          www.maribelschool.com
        </li>
      </ul>
    </div>
  </section>

  <section class="card card--back">
    <div class="brand" aria-hidden="true">
      <span class="brand__name">Maribel</span>
      <span class="brand__tagline">Language School</span>
    </div>
    <div class="band band--teal">
      <p class="address">12345, Address Goes Here Country Name, 123456.</p>
    </div>
  </section>
</main>
</body>
</html>
```